Business Card Design for Online Gift Business

Business card design for a new online Canadian company called "Harlow & Brine Gift Boxes" selling modern and luxurious gift boxes for every occasion. Items are sourced locally from talented socially-responsible Canadian artisans. Each gift is elegantly presented in a keepsake wood box to ensure a lasting impression.

Industry/Entity Type

E-Commerce

Contact Information for Business Card

Marla Whitcombe, Proprietor
Calgary, AB
403-555-2741
www.harlowandbrine.ca
hello@harlowandbrine.ca

Requirements
Must have
• Gifts from our best, to your best
• Please also include the symbols for Facebook and Instagram
Nice to have
• **I have attached a few samples of background colors and font colors that I like. I hope this helps in a few directions to try.

```html
<!DOCTYPE html>
<html lang="en">
<head>
<meta charset="UTF-8">
<title>Harlow &amp; Brine Gift Boxes – Business Card</title>
<link href="https://fonts.googleapis.com/css2?family=Open+Sans:wght@400;600;700&display=swap" rel="stylesheet">
<style>
  :root {
    --backdrop: #e6e3de;
    --card-front: #d3c6b1;
    --card-back: #ffffff;
    --ink-brown: #5a3d22;
    --brand-gold: #b39a74;
    --brand-brown: #7a5634;
  }
  * { margin: 0; padding: 0; box-sizing: border-box; }
  html, body {
    width: 1200px;
    height: 987px;
    overflow: hidden;
    background: var(--backdrop);
    font-family: "Open Sans", Arial, sans-serif;
  }
  .card {
    position: absolute;
    left: 293px;
    width: 615px;
    height: 352px;
    box-shadow: 0 2px 6px rgba(0,0,0,0.18);
  }
  .card--front { top: 124px; background: var(--card-front); }
  .card--back  { top: 511px; background: var(--card-back); }

  .brand {
    display: flex;
    align-items: center;
    gap: 12px;
    font-weight: 600;
    letter-spacing: 0.5px;
    white-space: nowrap;
  }
  .brand__dot {
    width: 22px;
    height: 22px;
    border-radius: 50%;
  }
  .card--front .brand {
    position: absolute;
    left: 44px;
    top: 70px;
    font-size: 34px;
    color: var(--brand-brown);
  }
  .card--front .brand__dot { background: var(--brand-brown); }

  .back-lockup {
    position: absolute;
    left: 50%;
    top: 50%;
    transform: translate(-50%, -50%);
    display: flex;
    flex-direction: column;
    align-items: center;
    gap: 14px;
  }
  .card--back .brand {
    font-size: 40px;
    color: var(--brand-gold);
  }
  .card--back .brand__dot { background: var(--brand-gold); }
  .tagline {
    font-size: 15px;
    font-weight: 400;
    letter-spacing: 1.5px;
    color: var(--brand-brown);
    white-space: nowrap;
  }

  .person {
    position: absolute;
    left: 40px;
    width: 240px;
    top: 250px;
    text-align: center;
    color: var(--ink-brown);
  }
  .person__name { font-size: 20px; font-weight: 700; line-height: 1.2; }
  .person__role { font-size: 15px; font-weight: 600; line-height: 1.4; }

  .contact {
    position: absolute;
    left: 377px;
    top: 200px;
    color: var(--ink-brown);
    font-size: 15px;
    font-weight: 600;
    list-style: none;
  }
  .contact li {
    display: flex;
    align-items: center;
    gap: 7px;
    height: 25px;
    white-space: nowrap;
  }
  .contact__city { margin-bottom: 3px; }
  .contact svg { width: 15px; height: 15px; flex: none; }
  .contact__social-dot {
    width: 15px;
    height: 15px;
    border-radius: 50%;
    background: var(--ink-brown);
    flex: none;
  }
</style>
</head>
<body>
  <section class="card card--front">
    <div class="brand"><span class="brand__dot"></span>Harlow &amp; Brine</div>

    <div class="person">
      <p class="person__name">Marla Whitcombe</p>
      <p class="person__role">Proprietor</p>
    </div>

    <ul class="contact">
      <li class="contact__city">Calgary, AB</li>
      <li>
        <svg viewBox="0 0 16 16" aria-hidden="true"><path fill="#5a3d22" d="M3.6 1.2l2.3 2.6-1.3 1.8c.9 2.2 2.7 4 4.9 4.9l1.8-1.3 2.6 2.3-1.4 2.3C7.4 13.6 2.4 8.6 1.3 3.6z"/></svg>
        403-555-2741
      </li>
      <li>
        <svg viewBox="0 0 16 16" aria-hidden="true"><circle cx="8" cy="8" r="7" fill="#5a3d22"/><path d="M1.5 8h13M8 1.2c-2.4 2-2.4 11.6 0 13.6M8 1.2c2.4 2 2.4 11.6 0 13.6" stroke="#d3c6b1" stroke-width="1.1" fill="none"/></svg>
        www.harlowandbrine.ca
      </li>
      <li>
        <svg viewBox="0 0 16 16" aria-hidden="true"><rect x="1" y="3" width="14" height="10" rx="1.5" fill="#5a3d22"/><path d="M1.8 4l6.2 5 6.2-5" stroke="#d3c6b1" stroke-width="1.2" fill="none"/></svg>
        hello@harlowandbrine.ca
      </li>
      <li>
        <span class="contact__social-dot" role="img" aria-label="Social network symbol"></span>
        <span class="contact__social-dot" role="img" aria-label="Social network symbol"></span>
        @harlowandbrine
      </li>
    </ul>
  </section>

  <section class="card card--back">
    <div class="back-lockup">
      <div class="brand"><span class="brand__dot"></span>Harlow &amp; Brine</div>
      <p class="tagline">Gifts from our best, to your best</p>
    </div>
  </section>
</body>
</html>
```